Business card design for a dynamic IT consulting company

We need a business card design for a young firm, specialized in the Telecommunications/Consulting industry. The name of the company is Quindor and Partners Business Consulting Ltd. (Short name: Quindor and Partnes)
Quindor = solve read reverse, so we aim to be uncomplicated and solution-oriented. The small pipe in our logo is also related to the word solve. So we need a new business card design, which is simple, eye catching and something non traditional (I would probably prefer a square shaped design rather than a rectangle, but open for suggestions). Attached our logo.

Target Market(s)

Usually our customers are Tier1 Telecoms providers (Q-Netra, Palorix, etc) and their executives.

Industry/Entity Type

Business

Contact Information for Business Card

Name: Bence Tolnavari
Email: b.tolnavari@quindor.hu
Web: www.quindor.hu
Mobile: +36 30 518 2769
Title: Managing Director

Optional:
Company name: Quindor and Partners Ltd.
Address: 1087 Budapest, Tolvenka str. 28/C, Hungary

Font styles to use
Other font styles liked:
• helveticaneue_medium, Prime Regular are used now.

Colors

Designer to choose colors to be used in the design.

Requirements
Must have
• I would like to have a 2 sided design.
Nice to have
• I thought if we make the logo a bit bigger (without the company name), that could go to the back with the company name below. I though, if the pipe in the logo is somehow touchable on the business card, would be nice and unique.

```html
<!DOCTYPE html>
<html lang="en">
<head>
<meta charset="utf-8">
<title>Quindor &amp; Partners – Business Card</title>
<link href="https://fonts.googleapis.com/css2?family=Exo+2:wght@400;500&family=Roboto:wght@400&display=swap" rel="stylesheet">
<style>
  :root {
    --canvas: #e4e4e6;
    --card-dark: #2e2e30;
    --card-light: #ffffff;
    --ink: #4a4a4c;
    --ink-soft: #5c5c5e;
    --magenta: #b5309a;
    --cyan: #139bd8;
    --slate: #5f5f61;
    --white: #ffffff;
  }
  * { box-sizing: border-box; margin: 0; padding: 0; }
  html, body {
    width: 1200px; height: 880px; overflow: hidden;
    background: var(--canvas);
  }
  .canvas { position: relative; width: 1200px; height: 880px; }

  .card {
    position: absolute; width: 600px; height: 343px; overflow: hidden;
    box-shadow: 0 10px 28px rgba(0,0,0,.18);
  }

  /* Back side */
  .card--back { left: 300px; top: 80px; background: var(--card-dark); }
  .card--back .texture {
    position: absolute; top: 0; right: 0; width: 300px; height: 343px;
    background: linear-gradient(200deg, #262628 0%, rgba(46,46,48,0) 70%);
  }
  .card--back .brand {
    position: absolute; left: 0; right: 0; top: 140px;
    display: flex; justify-content: center; align-items: center; gap: 12px;
    font-family: "Exo 2", sans-serif; font-weight: 400; font-size: 38px;
    color: var(--white); letter-spacing: .5px;
  }
  .card--back .brand-square { width: 14px; height: 14px; background: var(--magenta); }
  .card--back .web {
    position: absolute; left: 0; right: 0; top: 228px; text-align: center;
    font-family: "Roboto", sans-serif; font-size: 13px; letter-spacing: 3px;
    color: var(--white);
  }

  /* Front side */
  .card--front { left: 300px; top: 460px; background: var(--card-light); }
  .card--front .band {
    position: absolute; left: 0; top: 0; width: 130px; height: 100%;
    background: var(--card-dark);
    display: flex; align-items: center; justify-content: center;
  }
  .card--front .band-name {
    writing-mode: vertical-rl; transform: rotate(180deg);
    font-family: "Exo 2", sans-serif; font-weight: 400; font-size: 30px;
    color: var(--white); white-space: nowrap;
  }
  .card--front .stripe { position: absolute; left: 130px; width: 8px; }
  .stripe--cyan { top: 0; height: 50%; background: var(--cyan); }
  .stripe--magenta { top: 50%; height: 50%; background: var(--magenta); }

  .card--front .pattern {
    position: absolute; top: 0; right: 0; width: 210px; height: 343px;
    background: linear-gradient(160deg, rgba(181,48,154,.28) 0%, rgba(19,155,216,.22) 45%, rgba(95,95,97,.18) 75%, rgba(255,255,255,0) 100%);
  }

  .details { position: absolute; left: 176px; top: 118px; color: var(--ink); }
  .person-name {
    font-family: "Exo 2", sans-serif; font-weight: 500; font-size: 24px; color: var(--ink);
  }
  .person-title {
    font-family: "Roboto", sans-serif; font-size: 14px; color: var(--magenta); margin-top: 1px;
  }
  .contacts { list-style: none; margin-top: 16px; }
  .contacts li {
    display: flex; align-items: center; gap: 8px; height: 19px;
    font-family: "Roboto", sans-serif; font-size: 13px; color: var(--ink-soft);
  }
  .icon { width: 14px; height: 14px; display: block; }
  .address {
    margin-top: 12px; font-family: "Roboto", sans-serif; font-size: 13px;
    line-height: 18px; color: var(--ink-soft); font-style: normal;
  }
</style>
</head>
<body>
<main class="canvas">

  <section class="card card--back" aria-label="Card back">
    <div class="texture" role="img" aria-label="Faint dark tile decoration"></div>
    <div class="brand"><span class="brand-square"></span><span>Quindor &amp; Partners</span></div>
    <div class="web">www.quindor.hu</div>
  </section>

  <section class="card card--front" aria-label="Card front">
    <div class="band"><span class="band-name">Quindor &amp; Partners</span></div>
    <div class="stripe stripe--cyan"></div>
    <div class="stripe stripe--magenta"></div>
    <div class="pattern" role="img" aria-label="Scattered magenta, blue and grey tile decoration"></div>

    <div class="details">
      <h1 class="person-name">Bence Tolnavari</h1>
      <p class="person-title">Managing Director</p>
      <ul class="contacts">
        <li>
          <svg class="icon" viewBox="0 0 14 14"><rect width="14" height="14" fill="#b5309a"/><rect x="4" y="2.5" width="6" height="9" rx="1" fill="none" stroke="#fff" stroke-width="1.2"/></svg>
          +36 30 518 2769
        </li>
        <li>
          <svg class="icon" viewBox="0 0 14 14"><rect width="14" height="14" fill="#5f5f61"/><rect x="2.5" y="4" width="9" height="6" fill="none" stroke="#fff" stroke-width="1.1"/><path d="M2.5 4 L7 7.5 L11.5 4" fill="none" stroke="#fff" stroke-width="1.1"/></svg>
          b.tolnavari@quindor.hu
        </li>
        <li>
          <svg class="icon" viewBox="0 0 14 14"><rect width="14" height="14" fill="#139bd8"/><circle cx="7" cy="7" r="4" fill="none" stroke="#fff" stroke-width="1.1"/><path d="M3 7 H11 M7 3 C5 5 5 9 7 11 M7 3 C9 5 9 9 7 11" fill="none" stroke="#fff" stroke-width=".9"/></svg>
          www.quindor.hu
        </li>
      </ul>
      <address class="address">1087 Budapest<br>Tolvenka str. 28/C, Hungary</address>
    </div>
  </section>

</main>
</body>
</html>
```